SkyvornQ Business Cards and Stationary Design

Need a design for our business cards and stationary. I want to carry on the theme of the logo. I want the business cards to have a design on the back. I would like the business cards and the stationary to carry the same theme, design scheme, and branding

Target Market(s)

Airlines and Maintenance Facilities

Industry/Entity Type

Aviation

Contact Information for Business Card

Name
Position Title
Address: 4827 Trellis Hollow Road, Marlow Bay, Oregon, 97391
Office Number
Mobile Number
Email
Website

Font styles to use
Serif
Sans Serif

Colors

Designer to choose colors to be used in the design.

```html
<!DOCTYPE html>
<html lang="en">
<head>
<meta charset="utf-8">
<title>SkyvornQ Business Card</title>
<link href="https://fonts.googleapis.com/css2?family=Work+Sans:wght@400;500;700&display=swap" rel="stylesheet">
<style>
  :root {
    --backdrop: #2a2a2b;
    --card: #1c1c1d;
    --card-edge: #262627;
    --ink: #f2f2f2;
    --accent: #1f9be6;
    --accent-deep: #1b4fa8;
    --silver: #a9a9ab;
  }
  * { margin: 0; padding: 0; box-sizing: border-box; }
  html, body { width: 1200px; height: 900px; overflow: hidden; }
  body {
    background: var(--backdrop);
    font-family: "Work Sans", sans-serif;
    color: var(--ink);
    position: relative;
  }
  .card {
    position: absolute;
    width: 680px;
    height: 388px;
    background: linear-gradient(135deg, var(--card) 0%, var(--card-edge) 100%);
    box-shadow: 0 10px 30px rgba(0,0,0,0.45);
  }
  .card--back { left: 260px; top: 36px; }
  .card--front { left: 260px; top: 470px; }

  .back-brand {
    position: absolute;
    inset: 0;
    display: flex;
    flex-direction: column;
    align-items: center;
    justify-content: center;
    gap: 22px;
  }
  .back-brand .brand-circle {
    width: 96px; height: 96px;
    border: 6px solid var(--silver);
    border-radius: 50%;
  }
  .back-brand .brand-name {
    font-weight: 700;
    font-size: 46px;
    letter-spacing: 9px;
    color: var(--silver);
  }

  .front-brand {
    position: absolute;
    left: 0; top: 0;
    width: 352px; height: 100%;
    display: flex;
    flex-direction: column;
    align-items: center;
    justify-content: center;
    gap: 18px;
  }
  .front-brand .brand-circle {
    width: 92px; height: 92px;
    border: 6px solid var(--accent-deep);
    border-radius: 50%;
  }
  .front-brand .brand-name {
    font-weight: 700;
    font-size: 38px;
    letter-spacing: 7px;
    color: var(--ink);
  }
  .divider {
    position: absolute;
    left: 352px; top: 80px;
    width: 2px; height: 228px;
    background: var(--ink);
  }
  .contact {
    position: absolute;
    left: 384px; top: 82px;
    font-size: 17px;
    line-height: 1.35;
    letter-spacing: 0.6px;
  }
  .contact .person-name {
    font-weight: 500;
    font-size: 27px;
    letter-spacing: 2px;
    color: var(--accent);
    text-transform: uppercase;
    line-height: 1.1;
  }
  .contact .role { font-size: 16px; margin-bottom: 12px; }
  .contact .address { margin-bottom: 8px; }
  .contact .line { display: flex; align-items: center; gap: 10px; }
  .contact .line svg { width: 12px; height: 12px; flex: none; }
  .contact .web-name { color: var(--accent); }
</style>
</head>
<body>
  <section class="card card--back" aria-label="Card back">
    <div class="back-brand">
      <div class="brand-circle"></div>
      <div class="brand-name">SKYVORNQ</div>
    </div>
  </section>

  <section class="card card--front" aria-label="Card front">
    <div class="front-brand">
      <div class="brand-circle"></div>
      <div class="brand-name">SKYVORNQ</div>
    </div>
    <div class="divider"></div>
    <div class="contact">
      <div class="person-name">Dorian Keller</div>
      <div class="role">Director</div>
      <div class="address">4827 Trellis Hollow Road,<br>Marlow Bay, Oregon, 97391</div>
      <div class="line">
        <svg viewBox="0 0 12 12"><path d="M2.5 1l2 2.2-1 1.3c.7 1.5 1.8 2.6 3.2 3.3l1.3-1L10.2 9 9 11C5 10.5 1.5 7 1 3z" fill="var(--accent)"/></svg>
        <span>555-302-0186</span>
      </div>
      <div class="line">
        <svg viewBox="0 0 12 12"><rect x="1" y="2.5" width="10" height="7" fill="none" stroke="var(--accent)" stroke-width="1.2"/><path d="M1 2.5l5 4 5-4" fill="none" stroke="var(--accent)" stroke-width="1.2"/></svg>
        <span>info@skyvornq.com</span>
      </div>
      <div class="line">
        <svg viewBox="0 0 12 12"><circle cx="6" cy="6" r="5" fill="none" stroke="var(--accent)" stroke-width="1.1"/><ellipse cx="6" cy="6" rx="2.2" ry="5" fill="none" stroke="var(--accent)" stroke-width="1"/><path d="M1 6h10" stroke="var(--accent)" stroke-width="1"/></svg>
        <span>www.<span class="web-name">skyvornq</span>.com</span>
      </div>
    </div>
  </section>
</body>
</html>
```